Brindle Sky Port needs a new upscale business card design for our high end aircraft hangar complex

Brindle Sky Port (BSP) is a large, upscale jet hangar complex in the US housing expensive aircraft. We need a new business card design, using our current logo. We will be attending a industry convention and need a card design that will stand out and be remembered by aircraft owners and private pilots.

Target Market(s)

Aircraft pilots or owners looking for a new upscale hangar

Industry/Entity Type

Airport

Contact Information for Business Card

I like to use very heavy card stock, 400#, double sided. Square, no rounded edges please.

Colors
3276b5
0255a3
85abd2

Requirements
Must have
• An expensive, classy design, vivid colors.
Nice to have
• Needs to look very expensive and classy, and have some "pop". Designer must be able to download or copy my current typeface or fonts.
• One card side might be black with the "Logo and Brindle Sky Port Double line image in blue (or try gold, or glossy black), and perhaps have a grayed out "K720 jet silhouette". The other card side would have our contact info, and perhaps the "BSP Logo only". I'd like my contact info 'stacked', not in a paragraph format.
Should not have
• Should not look "too busy". Having a double-sided card will help.

```html
<!DOCTYPE html>
<html lang="en">
<head>
<meta charset="UTF-8">
<title>Brindle Sky Port – Business Card</title>
<link href="https://fonts.googleapis.com/css2?family=Open+Sans:wght@400;600;700&display=swap" rel="stylesheet">
<style>
  :root {
    --backdrop: #000000;
    --paper: #efefef;
    --brand-blue: #1f69a8;
    --brand-blue-deep: #0d5a9c;
    --card-blue: #2773ad;
    --ink: #3a3a3a;
    --white: #ffffff;
  }
  * { margin: 0; padding: 0; box-sizing: border-box; }
  html, body {
    width: 1200px;
    height: 900px;
    overflow: hidden;
    background: var(--backdrop);
    font-family: "Open Sans", Arial, sans-serif;
  }
  .canvas {
    position: relative;
    width: 1200px;
    height: 900px;
  }
  .card {
    position: absolute;
    top: 200px;
    width: 310px;
    height: 500px;
    border-radius: 0;
  }
  .card-front {
    left: 265px;
    background: var(--paper);
  }
  .card-back {
    left: 640px;
    background: var(--card-blue);
  }
  .brand-mark {
    position: absolute;
    top: 56px;
    left: 0;
    width: 100%;
    text-align: center;
    color: var(--brand-blue);
  }
  .brand-initials {
    font-size: 58px;
    font-weight: 700;
    line-height: 1;
    letter-spacing: 2px;
  }
  .brand-name {
    margin-top: 12px;
    font-size: 22px;
    font-weight: 700;
    line-height: 1;
  }
  .contact {
    position: absolute;
    left: 35px;
    top: 282px;
    color: var(--ink);
  }
  .contact-name {
    font-size: 18px;
    line-height: 22px;
    color: var(--brand-blue);
  }
  .contact-title {
    font-size: 13px;
    line-height: 18px;
  }
  .contact-address {
    margin-top: 11px;
    font-size: 13px;
    line-height: 18px;
  }
  .contact-list {
    list-style: none;
    margin-top: 18px;
    font-size: 13px;
  }
  .contact-list li {
    display: flex;
    align-items: center;
    height: 20.7px;
  }
  .contact-list svg {
    width: 10px;
    height: 10px;
    margin-right: 10px;
    fill: var(--brand-blue-deep);
  }
  .back-initials {
    position: absolute;
    right: 62px;
    bottom: 56px;
    font-size: 82px;
    font-weight: 700;
    line-height: 1;
    letter-spacing: 3px;
    color: var(--white);
  }
</style>
</head>
<body>
<main class="canvas">
  <section class="card card-front">
    <div class="brand-mark">
      <div class="brand-initials">BSP</div>
      <div class="brand-name">Brindle Sky Port</div>
    </div>
    <div class="contact">
      <p class="contact-name">Marcus Delane</p>
      <p class="contact-title">Managing Director</p>
      <p class="contact-address">12345, Address Goes Here<br>Country Name, 123456.</p>
      <ul class="contact-list">
        <li><svg viewBox="0 0 10 10" aria-hidden="true"><path d="M2 0.5l1.6 2.2-1 1c.6 1.3 1.5 2.2 2.7 2.7l1-1L9.5 7 8.3 9.3C4 9 1 6 .7 1.7z"/></svg>(044)-456-7890</li>
        <li><svg viewBox="0 0 10 10" aria-hidden="true"><rect x="0.5" y="3" width="9" height="6" rx="1"/><rect x="2.5" y="0.5" width="5" height="3"/></svg>123-456-7890</li>
        <li><svg viewBox="0 0 10 10" aria-hidden="true"><path d="M0.5 2h9v6h-9z M0.5 2l4.5 3.5L9.5 2"/></svg>info@youremail.com</li>
        <li><svg viewBox="0 0 10 10" aria-hidden="true"><circle cx="5" cy="5" r="4.5"/></svg>www.website.com</li>
      </ul>
    </div>
  </section>
  <section class="card card-back">
    <div class="back-initials">BSP</div>
  </section>
</main>
</body>
</html>
```